FLUSH COMET the solution to twinkle the smell away...because everyone poops

I need a label for my handmade poop spray. Flush comet is an organic blend of essential oils that eliminates the odor when you poop. Directions must be on the back of the label : shake well before each use. Spray on the toilet water surface 4-6 times to cover the water before you go. Poop as usual and flush. Safe for all pipes and sewer systems. To order visit my Crafto shop enter flush comet

Font styles to use
Decorative

Requirements
Must have
• Directions on how to use
Nice to have
• Elegant design label. Product is meant to be kept in the bathroom

```html
<!DOCTYPE html>
<html lang="en">
<head>
<meta charset="UTF-8">
<title>Flush Comet – Bottle Label</title>
<link href="https://fonts.googleapis.com/css2?family=Source+Sans+3:wght@600;700;800&family=Lato:ital,wght@1,700&display=swap" rel="stylesheet">
<style>
  :root {
    --backdrop: #1b1a1c;
    --label-gold: #f4a917;
    --label-gold-deep: #e8960c;
    --label-edge: #d98a0a;
    --ink-white: #ffffff;
    --ribbon-text: #f0a012;
    --ornament-tone: rgba(255, 246, 225, 0.28);
  }
  * { box-sizing: border-box; margin: 0; padding: 0; }
  html, body {
    width: 1200px;
    height: 901px;
    overflow: hidden;
    background: var(--backdrop);
  }
  .canvas {
    position: relative;
    width: 1200px;
    height: 901px;
    display: flex;
    align-items: center;
    justify-content: center;
  }
  .label {
    position: relative;
    width: 560px;
    height: 830px;
    border-radius: 16px;
    background: linear-gradient(180deg, var(--label-gold) 0%, var(--label-gold-deep) 100%);
    box-shadow: inset 0 0 0 3px var(--label-edge);
    color: var(--ink-white);
    text-align: center;
  }
  .ornament-area {
    position: absolute;
    left: 50%;
    top: 165px;
    width: 220px;
    height: 285px;
    transform: translateX(-50%);
    border-radius: 12px;
    background: radial-gradient(ellipse at 50% 55%, var(--ornament-tone) 0%, rgba(255, 246, 225, 0.12) 55%, rgba(255, 246, 225, 0) 80%);
  }
  .product-name {
    position: absolute;
    left: 0;
    right: 0;
    top: 470px;
    font-family: "Source Sans 3", sans-serif;
    font-weight: 800;
    font-size: 62px;
    letter-spacing: 1px;
    line-height: 1;
  }
  .ribbon {
    position: absolute;
    left: 50%;
    top: 543px;
    width: 340px;
    height: 48px;
    transform: translateX(-50%);
  }
  .ribbon svg { position: absolute; inset: 0; }
  .ribbon-text {
    position: relative;
    display: block;
    line-height: 44px;
    font-family: "Source Sans 3", sans-serif;
    font-weight: 700;
    font-size: 27px;
    color: var(--ribbon-text);
    letter-spacing: 1px;
  }
  .tagline {
    position: absolute;
    left: 0;
    right: 0;
    top: 608px;
    font-family: "Lato", sans-serif;
    font-style: italic;
    font-weight: 700;
    font-size: 24px;
  }
  .directions {
    position: absolute;
    left: 50px;
    right: 50px;
    bottom: 38px;
    font-family: "Lato", sans-serif;
    font-style: italic;
    font-weight: 700;
    font-size: 13px;
    line-height: 1.45;
  }
</style>
</head>
<body>
  <main class="canvas">
    <section class="label">
      <div class="ornament-area" role="img" aria-label="White swirled tree ornament topped by a star"></div>
      <h1 class="product-name">FLUSH COMET</h1>
      <div class="ribbon">
        <svg viewBox="0 0 340 48" width="340" height="48" aria-hidden="true">
          <polygon points="0,6 22,24 0,42 40,42 40,6" fill="#ffffff"/>
          <polygon points="340,6 318,24 340,42 300,42 300,6" fill="#ffffff"/>
          <rect x="26" y="0" width="288" height="44" fill="#ffffff"/>
        </svg>
        <span class="ribbon-text">BEFORE-YOU-GO SPRAY</span>
      </div>
      <p class="tagline">"Twinkle the smell away"</p>
      <p class="directions">Directions: shake well. Spray 4–6 times on the toilet water before you go. Poop as usual and flush. Safe for all pipes and sewers.</p>
    </section>
  </main>
</body>
</html>
```